KVM Contracting services . Building and maintenance services, optic fibre installation

Business cards and logo design.I need a logo that I can use on business cards ,workwear and on my vehicles. I would like the KVM to be the main or larger text and contracting services to be the smaller or less important text.I like monograms, modern designs and repeating patterns symbols. I am also a Gemini and my favourite number is 22 so if this can be any inspiration to help with the design. Am thinking of the using German flag colours as a his is my family’s heritage. And the other 2 main colours I wear is black and white.But any ideas are appreciated.I do not need a design that is trade specific but a design that could be used for any business.

Target Market(s)

General public

Contact Information for Business Card

KVM Contracting Services ( front of business card)

(Back of business card)
Darren Holtwick
0451907326
Maintenance services
Optic fibre and data installation

Logo Text

Logo can just be pattern or monogram or incorporate KVM . I like the gemini star sign and the number 22

Colors
ec1f27
000000
fbee3e
ffffff

Requirements
Must have
• Logo and KVM Contracting Services on the front of business card
Nice to have
• Possible use of German flag colours.
• Modern design.
• Design to be able to be used on black or white background as I want to put it on clothing

```html
<!DOCTYPE html>
<html lang="en">
<head>
<meta charset="utf-8">
<title>KVM Contracting Services – Business Cards</title>
<link href="https://fonts.googleapis.com/css2?family=Montserrat:wght@800&family=Open+Sans:wght@400&display=swap" rel="stylesheet">
<style>
  :root {
    --red: #ec1f27;
    --black: #000000;
    --yellow: #fbee3e;
    --white: #ffffff;
    --backdrop: #e9e6e1;
    --ink: #1a1a1a;
  }
  * { box-sizing: border-box; margin: 0; padding: 0; }
  html, body {
    width: 1200px;
    height: 900px;
    overflow: hidden;
    background: var(--backdrop);
  }
  .canvas {
    width: 1200px;
    height: 900px;
    display: flex;
    align-items: center;
    justify-content: center;
    gap: 40px;
  }
  .card {
    position: relative;
    width: 540px;
    height: 330px;
    overflow: hidden;
    box-shadow: 0 6px 18px rgba(0, 0, 0, 0.18);
  }

  /* Front */
  .card--front {
    background: var(--black);
    display: flex;
    align-items: center;
    justify-content: center;
  }
  .brand {
    display: flex;
    align-items: center;
    gap: 18px;
    color: var(--red);
    font-family: "Montserrat", sans-serif;
    font-weight: 800;
  }
  .brand__dot {
    width: 64px;
    height: 64px;
    border-radius: 50%;
    background: var(--red);
    flex: none;
  }
  .brand__words { display: flex; flex-direction: column; line-height: 1; }
  .brand__name { font-size: 72px; letter-spacing: 10px; }
  .brand__tagline { font-size: 12.5px; letter-spacing: 0.4px; margin-top: 6px; }

  /* Back */
  .card--back { background: var(--white); }
  .card__wave { position: absolute; inset: 0; width: 100%; height: 100%; }
  .contact {
    position: absolute;
    left: 38px;
    top: 74px;
  }
  .contact__name {
    font-family: "Montserrat", sans-serif;
    font-weight: 800;
    font-size: 18px;
    color: var(--red);
    letter-spacing: 0.3px;
  }
  .contact__phone {
    font-family: "Open Sans", sans-serif;
    font-size: 20px;
    color: var(--ink);
    letter-spacing: 1px;
    margin-top: 6px;
  }
  .card--back .brand {
    position: absolute;
    right: 34px;
    top: 52px;
    gap: 12px;
  }
  .card--back .brand__dot { width: 44px; height: 44px; }
  .card--back .brand__name { font-size: 50px; letter-spacing: 6px; }
  .card--back .brand__tagline { font-size: 9px; margin-top: 4px; }
  .services {
    position: absolute;
    left: 76px;
    top: 172px;
    list-style: none;
    font-family: "Open Sans", sans-serif;
    font-size: 15px;
    line-height: 1.3;
    color: var(--ink);
  }
</style>
</head>
<body>
  <main class="canvas">
    <section class="card card--front" aria-label="Business card front">
      <div class="brand">
        <span class="brand__dot" aria-hidden="true"></span>
        <div class="brand__words">
          <span class="brand__name">KVM</span>
          <span class="brand__tagline">CONTRACTING SERVICES</span>
        </div>
      </div>
    </section>

    <section class="card card--back" aria-label="Business card back">
      <svg class="card__wave" viewBox="0 0 540 330" preserveAspectRatio="none" aria-hidden="true">
        <path d="M0,300 C180,305 360,235 540,152 L540,330 L0,330 Z" fill="var(--black)"/>
        <path d="M0,291 C170,299 330,256 452,184" fill="none" stroke="var(--white)" stroke-width="6"/>
        <path d="M0,268 C170,280 340,248 452,184 C330,256 170,299 0,291 Z" fill="var(--red)"/>
      </svg>

      <div class="contact">
        <p class="contact__name">DARREN HOLTWICK</p>
        <p class="contact__phone">0451907326</p>
      </div>

      <div class="brand">
        <span class="brand__dot" aria-hidden="true"></span>
        <div class="brand__words">
          <span class="brand__name">KVM</span>
          <span class="brand__tagline">CONTRACTING SERVICES</span>
        </div>
      </div>

      <ul class="services">
        <li>Maintenance services</li>
        <li>Optic fibre and data installation</li>
      </ul>
    </section>
  </main>
</body>
</html>
```